Real Estate Brokerage Stationery Designs

I am looking to have presentation folders with business card slots on both sides along with pockets on both sides. I've attached logos, website colors along with current business card designs.

I am looking for envelope designs both big and small. Possibly new business card designs, notepad templates for big and small notepads. Letterhead designs. Pop socket designs. Realtors name badge designs.

www.brightholdrealty.example

```html
<!DOCTYPE html>
<html lang="en">
<head>
<meta charset="utf-8">
<title>Brighthold Realty Stationery</title>
<link rel="stylesheet" href="https://fonts.googleapis.com/css2?family=Questrial&family=Roboto:wght@400;500;700&display=swap">
<style>
:root{
  --frame:#000;
  --stage:#dcdcdc;
  --paper:#f1f1f1;
  --paper-light:#f6f6f6;
  --card:#ffffff;
  --brand-blue:#0a4fa6;
  --ink:#1c1c1c;
  --body-ink:#5a5a5a;
  --photo-top:#cfcfcf;
  --photo-bottom:#2a2a2a;
}
*{box-sizing:border-box;margin:0;padding:0}
html,body{width:1200px;height:1200px;overflow:hidden;background:var(--frame)}
.canvas{position:relative;width:1200px;height:1200px;background:var(--frame)}
.stage{position:absolute;left:0;top:154px;width:1200px;height:914px;background:var(--stage)}
.sheet{position:absolute;box-shadow:0 1px 4px rgba(0,0,0,.18)}
.wordmark{font-family:"Roboto",sans-serif;font-weight:700;color:var(--ink);display:flex;align-items:center;gap:6px;white-space:nowrap}
.wordmark .mark{display:inline-block;background:var(--brand-blue)}
.address{font-family:"Roboto",sans-serif;font-weight:400;color:var(--ink);text-align:center}

/* Letterhead */
.letterhead{left:51px;top:216px;width:555px;height:784px;background:var(--paper)}
.letterhead .head{position:absolute;left:0;right:0;top:128px}
.letterhead .wordmark{justify-content:center;font-size:26px}
.letterhead .wordmark .mark{width:20px;height:20px}
.letterhead .address{position:absolute;left:0;right:0;top:170px;font-size:7.6px;line-height:10.5px}
.letter{position:absolute;left:50px;top:220px;width:451px;font-family:"Questrial",sans-serif;color:var(--body-ink)}
.letter .salutation{font-size:14px;color:#555;margin-bottom:24px}
.letter p{font-size:8.3px;line-height:12px;text-align:justify;margin-bottom:12px}
.letter .closing{margin-top:24px;font-size:8.3px}
.signature{position:absolute;left:42px;top:548px;width:100px;height:40px;background:linear-gradient(90deg,#dfe6f1,#e9edf3);border-radius:4px}
.letter-footer{position:absolute;left:0;bottom:0;width:555px;height:34px}
.letter-footer .col{position:absolute;top:6px;font-family:"Roboto",sans-serif;font-size:7.2px;color:#fff;line-height:11px;white-space:nowrap}
.letter-footer .col-phones{left:48px}
.letter-footer .col-fax{left:130px}
.letter-footer .col-web{left:236px}
.contact-line{display:flex;align-items:center;gap:3px}
.contact-line svg{flex:none}

/* Business card front */
.card-front{left:616px;top:216px;width:268px;height:162px;background:var(--card);overflow:hidden}
.card-front .wordmark{position:absolute;left:22px;top:40px;font-size:12px;gap:4px}
.card-front .wordmark .mark{width:9px;height:9px}
.card-band{position:absolute;left:0;top:65px;width:268px;height:23px;background:var(--brand-blue)}
.card-band .name{position:absolute;left:21px;top:3px;font-family:"Roboto",sans-serif;font-weight:700;font-size:10.5px;color:#fff;letter-spacing:.2px}
.card-band .role{position:absolute;left:21px;top:14.5px;font-family:"Roboto",sans-serif;font-size:5px;color:#fff}
.badge{position:absolute;top:5px;background:#fff;border-radius:1px}
.portrait{position:absolute;left:170px;top:0;width:98px;height:162px;background:linear-gradient(180deg,var(--photo-top) 0%,#8a8a8a 45%,var(--photo-bottom) 100%)}
.card-details{position:absolute;left:21px;top:94px;font-family:"Roboto",sans-serif;font-size:6px;color:var(--ink);line-height:8px}
.card-details .addr{margin-bottom:3px}
.card-details .contact-line{gap:4px}

/* Business card back */
.card-back{left:901px;top:216px;width:268px;height:162px;background:var(--card)}
.card-back .wordmark{position:absolute;left:0;right:0;top:90px;justify-content:center;font-size:17px}
.card-back .wordmark .mark{width:13px;height:13px}
.tagline{font-family:"Roboto",sans-serif;text-align:center}
.card-back .tagline{position:absolute;left:0;right:0;top:126px;font-size:6.5px;line-height:9.5px;color:var(--ink)}
.sep{color:var(--brand-blue);padding:0 3px}

/* Envelope back */
.envelope-back{left:615px;top:433px;width:553px;height:252px;background:var(--paper-light)}
.envelope-back .flap{position:absolute;left:0;top:0}
.envelope-back .tagline{position:absolute;left:0;right:0;top:210px;font-size:10px;line-height:14px;color:var(--brand-blue)}

/* Envelope front */
.envelope-front{left:615px;top:739px;width:556px;height:254px;background:var(--paper-light)}
.envelope-front .wordmark{position:absolute;left:22px;top:80px;font-size:15px;gap:4px}
.envelope-front .wordmark .mark{width:11px;height:11px}
.envelope-front .address{position:absolute;left:22px;width:134px;top:117px;font-size:6.2px;line-height:8px}
</style>
</head>
<body>
<div class="canvas">
  <div class="stage"></div>

  <!-- Letterhead -->
  <section class="sheet letterhead">
    <div class="head">
      <div class="wordmark"><span class="mark"></span>Brighthold Realty</div>
    </div>
    <div class="address">2400 Harbor Point Dr,<br>Suite 310, Lakeview FL 33400</div>

    <div class="letter">
      <div class="salutation">Dear Mr. Smith,</div>
      <p>Lorem ipsum dolor sit amet, consectetur adipiscing elit. Donec orci purus, luctus vitae dignissim eu, iaculis sed purus. Vivamus faucibus, ipsum nec aliquet viverra, leo mauris condimentum ligula, sit amet sagittis enim ligula quis arcu. Nam egestas tortor id nisi porttitor mattis. In tortor ante, ultricies in suscipit a, tempus non massa. Vivamus et auctor mi. Fusce vel massa nulla. Phasellus nec eros mauris, et scelerisque orci.</p>
      <p>Donec malesuada orci vitae nulla accumsan porta a id massa. Quisque accumsan iaculis magna sit amet fringilla. Maecenas consequat, magna eget tincidunt semper, odio nibh rutrum mi, id feugiat ante nisi eu risus. Vestibulum nunc orci, rhoncus a placerat in, ultricies in mi. Cras mattis varius eros, vel fringilla nisi suscipit eget. Quisque scelerisque sagittis nulla at porttitor.</p>
      <p>Sed id augue vitae urna euismod commodo aliquet a quam. Pellentesque arcu velit, cursus et malesuada ut, consequat et diam. Nullam erat sem, rhoncus id ullamcorper vitae, rhoncus et arcu. In ultricies ultricies nulla, ut rutrum nisi iaculis at. Donec eu magna a metus ornare faucibus. Fusce aliquet faucibus ultricies. Morbi semper, est id tincidunt gravida, sem arcu adipiscing lacus, ac bibendum nulla leo eu purus. Quisque nec diam sed risus consectetur a ccumsan quis quis nibh. Vestibulum id purus lorem.</p>
      <p>It is a long established fact that a reader will be distracted by the readable content of a page when looking at its layout. The point of using Lorem Ipsum is that it has a more-or-less normal distribution of letters, as opposed to using 'Content here, content here', making it look like readable English. Many desktop publishing packages</p>
      <div class="closing">Sincerely,</div>
    </div>
    <div class="signature" role="img" aria-label="Handwritten signature"></div>

    <footer class="letter-footer">
      <svg width="555" height="34" viewBox="0 0 555 34" style="position:absolute;left:0;top:0"><polygon points="0,0 355,0 375,34 0,34" fill="var(--brand-blue)"/></svg>
      <div class="col col-phones">
        <div class="contact-line"><svg width="5" height="7" viewBox="0 0 5 7"><rect x=".5" y=".5" width="4" height="6" rx=".8" fill="none" stroke="#fff"/></svg>555-010-2481</div>
        <div class="contact-line"><svg width="6" height="6" viewBox="0 0 6 6"><path d="M1 .5 2.2 2 1.6 2.8Q2.6 4.4 3.4 4.4L4.1 3.8 5.5 5 4.8 5.8Q.2 5 .2 1.2Z" fill="#fff"/></svg>555-010-3392</div>
      </div>
      <div class="col col-fax">
        <div class="contact-line"><svg width="7" height="6" viewBox="0 0 7 6"><rect x="1.5" y="0" width="4" height="2" fill="#fff"/><rect x="0" y="2" width="7" height="3" rx=".5" fill="#fff"/></svg>555-010-4470</div>
        <div class="contact-line"><svg width="7" height="6" viewBox="0 0 7 6"><rect x=".5" y=".5" width="6" height="5" rx=".6" fill="none" stroke="#fff"/><path d="M.8 1 3.5 3.3 6.2 1" fill="none" stroke="#fff"/></svg>mh@brightholdrealty.example</div>
      </div>
      <div class="col col-web">
        <div class="contact-line"><svg width="7" height="7" viewBox="0 0 7 7"><circle cx="3.5" cy="3.5" r="3" fill="none" stroke="#fff" stroke-width=".8"/><path d="M.5 3.5H6.5M3.5 .5V6.5" stroke="#fff" stroke-width=".6"/></svg>www.brightholdrealty.example</div>
      </div>
    </footer>
  </section>

  <!-- Business card front -->
  <section class="sheet card-front">
    <div class="wordmark"><span class="mark"></span>Brighthold Realty</div>
    <div class="card-band">
      <div class="name">MARCUS HALE</div>
      <div class="role">REALTOR®</div>
      <div class="badge" style="left:121px;width:11px;height:12px"></div>
      <div class="badge" style="left:137px;width:26px;height:12px"></div>
    </div>
    <div class="portrait" role="img" aria-label="Portrait photo of the realtor in a dark suit"></div>
    <div class="card-details">
      <div class="addr">2400 Harbor Point Dr,<br>Suite 310, Lakeview FL 33400</div>
      <div class="contact-line"><svg width="4" height="6" viewBox="0 0 4 6"><rect x=".4" y=".4" width="3.2" height="5.2" rx=".6" fill="none" stroke="var(--brand-blue)" stroke-width=".8"/></svg>555-010-2481</div>
      <div class="contact-line"><svg width="5" height="5" viewBox="0 0 6 6"><path d="M1 .5 2.2 2 1.6 2.8Q2.6 4.4 3.4 4.4L4.1 3.8 5.5 5 4.8 5.8Q.2 5 .2 1.2Z" fill="var(--brand-blue)"/></svg>555-010-3392</div>
      <div class="contact-line"><svg width="5" height="5" viewBox="0 0 7 6"><rect x="1.5" y="0" width="4" height="2" fill="var(--brand-blue)"/><rect x="0" y="2" width="7" height="3" rx=".5" fill="var(--brand-blue)"/></svg>555-010-4470</div>
      <div class="contact-line"><svg width="5" height="5" viewBox="0 0 7 6"><rect x="0" y=".5" width="7" height="5" rx=".6" fill="var(--brand-blue)"/></svg>mh@brightholdrealty.example</div>
      <div class="contact-line"><svg width="5" height="5" viewBox="0 0 7 7"><circle cx="3.5" cy="3.5" r="3.2" fill="var(--brand-blue)"/></svg>www.brightholdrealty.example</div>
    </div>
  </section>

  <!-- Business card back -->
  <section class="sheet card-back">
    <div class="wordmark"><span class="mark"></span>Brighthold Realty</div>
    <div class="tagline">Residential Real Estate<span class="sep">|</span>Commercial Real Estate<br>Property Management<span class="sep">|</span>Investments</div>
  </section>

  <!-- Envelope back -->
  <section class="sheet envelope-back">
    <svg class="flap" width="553" height="82" viewBox="0 0 553 82"><path d="M0 0H553L545 18Q537 72 505 81H40Q14 74 8 18Z" fill="var(--brand-blue)"/></svg>
    <div class="tagline">Residential Real Estate<span class="sep">|</span>Commercial Real Estate<br>Property Management<span class="sep">|</span>Investments</div>
  </section>

  <!-- Envelope front -->
  <section class="sheet envelope-front">
    <div class="wordmark"><span class="mark"></span>Brighthold Realty</div>
    <div class="address">2400 Harbor Point Dr,<br>Suite 310, Lakeview FL 33400</div>
  </section>
</div>
</body>
</html>
```